Investment Management Firm Power point template

Marrow Holdings is a real estate investment firm focused on buying commercial office and residential property in the UK. We produce powerpoint presentations for our Board of Directors, Investment Committee and also to external investors.

We are looking for a powerpoint design template which we can use for future presentations which provide a professional look and feel.

Our current website: http://www.marrowholdings.example.co.uk/

Target Market(s)

Institution Investors, Board of Directors, Professionals

Industry/Entity Type

Real Estate

Requirements
Must have
• Leverage off the current logo and colour scheme. However, does not have to purely rely on this colour scheme.
• - Title page
• - Content Page
• - Slide where graphs can be incorporated
• - Slide where photos can be incorporated
• - Slide of UK Map which can show where the property portfolio is currently located
• - Other slides incorporating smart art or other designs that can be used for future presentations
Nice to have
• An example of graphics that we would love to have in the powerpoint pack which we can easily edit has been attached

```html
<!DOCTYPE html>
<html lang="en">
<head>
<meta charset="utf-8">
<title>Slide Title Here</title>
<link href="https://fonts.googleapis.com/css2?family=Fira+Sans:ital,wght@0,300;0,400;0,700;1,600&display=swap" rel="stylesheet">
<style>
  :root {
    --navy: #0e4c7d;
    --text: #2b2b2b;
    --band: #2b6a96;
    --circle-dark: #1c1c1c;
    --circle-grey: #555555;
    --circle-teal: #2a87a6;
    --circle-navy: #0a5878;
    --white: #ffffff;
  }
  html, body {
    margin: 0;
    padding: 0;
    overflow: hidden;
  }
  body {
    width: 1200px;
    height: 900px;
    background: var(--white);
    font-family: "Fira Sans", Arial, sans-serif;
    color: var(--text);
  }
  .slide {
    position: relative;
    width: 1200px;
    height: 900px;
    overflow: hidden;
  }
  .slide-title {
    position: absolute;
    left: 34px;
    top: 28px;
    margin: 0;
    font-size: 34px;
    font-weight: 700;
    color: var(--navy);
    letter-spacing: 0.2px;
  }
  .title-rule {
    position: absolute;
    left: 0;
    top: 72px;
    width: 290px;
    height: 3px;
    background: var(--navy);
  }
  .body-copy {
    position: absolute;
    left: 78px;
    top: 209px;
    width: 480px;
    font-size: 19.5px;
    line-height: 33px;
    font-weight: 400;
  }
  .body-copy p {
    margin: 0 0 33px;
  }
  .body-copy .lead {
    color: var(--navy);
    font-style: italic;
    font-weight: 600;
  }
  .stat-graphic {
    position: absolute;
    left: 630px;
    top: 200px;
    width: 500px;
    height: 500px;
  }
  .footer-band {
    position: absolute;
    left: 0;
    bottom: 0;
    width: 1200px;
    height: 57px;
    background: var(--band);
  }
  .brand-box {
    position: absolute;
    left: 918px;
    top: 841px;
    width: 275px;
    height: 55px;
    background: var(--white);
    display: flex;
    align-items: center;
    justify-content: center;
    gap: 12px;
  }
  .brand-square {
    width: 22px;
    height: 22px;
    background: var(--navy);
  }
  .brand-name {
    font-size: 26px;
    font-weight: 400;
    color: var(--navy);
  }
</style>
</head>
<body>
<main class="slide">
  <h1 class="slide-title">Slide Title Here</h1>
  <div class="title-rule"></div>

  <section class="body-copy">
    <p>While a property’s fundamentals are important to us, we put equal focus on the people who use and enjoy our spaces. The experience of being in our buildings — from design to atmosphere — is strategically planned. Functionality and efficiency are crucial and technology is in our DNA.</p>
    <p class="lead">With these fundamental characteristics in mind we strive to create businesses around our properties</p>
    <p>As part of the Thornbury Ashcroft Group we directly and indirectly benefit from the ecosystem of companies around us. Thornbury Ashcroft brings unrivalled expertise in building successful, long-lasting businesses.</p>
  </section>

  <svg class="stat-graphic" viewBox="0 0 500 500" xmlns="http://www.w3.org/2000/svg" font-family="Fira Sans, Arial, sans-serif">
    <g class="circles">
      <circle cx="141" cy="143" r="126" fill="#1c1c1c" opacity="0.95"/>
      <circle cx="363" cy="143" r="126" fill="#555555" opacity="0.92"/>
      <circle cx="141" cy="367" r="126" fill="#2a87a6" opacity="0.95"/>
      <circle cx="363" cy="367" r="126" fill="#0a5878" opacity="0.95"/>
    </g>
    <g class="rules" stroke="#ffffff" stroke-width="1" opacity="0.7">
      <line x1="57" y1="79" x2="223" y2="79"/><line x1="57" y1="85" x2="223" y2="85"/>
      <line x1="57" y1="214" x2="223" y2="214"/><line x1="57" y1="220" x2="223" y2="220"/>
      <line x1="279" y1="79" x2="445" y2="79"/><line x1="279" y1="85" x2="445" y2="85"/>
      <line x1="279" y1="214" x2="445" y2="214"/><line x1="279" y1="220" x2="445" y2="220"/>
      <line x1="57" y1="303" x2="223" y2="303"/><line x1="57" y1="309" x2="223" y2="309"/>
      <line x1="57" y1="438" x2="223" y2="438"/><line x1="57" y1="444" x2="223" y2="444"/>
      <line x1="279" y1="303" x2="445" y2="303"/><line x1="279" y1="309" x2="445" y2="309"/>
      <line x1="279" y1="438" x2="445" y2="438"/><line x1="279" y1="444" x2="445" y2="444"/>
    </g>
    <text x="141" y="172" text-anchor="middle" fill="#ffffff" font-weight="300"><tspan font-size="88">70</tspan><tspan font-size="40">%</tspan></text>
    <text x="363" y="396" text-anchor="middle" fill="#ffffff" font-weight="300"><tspan font-size="88">30</tspan><tspan font-size="40">%</tspan></text>
    <g fill="#ffffff" font-size="18" text-anchor="middle">
      <text x="363" y="113">Lorem ipsum dolor</text>
      <text x="363" y="140">sit Lorem ipsum</text>
      <text x="363" y="167">dolor sit Lorem</text>
      <text x="363" y="194">ipsum dolor sit</text>
      <text x="141" y="337">Lorem ipsum dolor</text>
      <text x="141" y="364">sit Lorem ipsum</text>
      <text x="141" y="391">dolor sit Lorem</text>
      <text x="141" y="418">ipsum dolor sit</text>
    </g>
  </svg>

  <footer class="footer-band"></footer>
  <div class="brand-box">
    <span class="brand-square"></span>
    <span class="brand-name">Marrow Holdings</span>
  </div>
</main>
</body>
</html>
```